Website for Ashcombe Tube Drift

Require a website for a river float in the City of Edmonton. Located on North Saskatchewan River. Will need to be a coded website with incorporated booking system through Fare Harbor software.

Pages include
Home
Pricing
About
FAQ
Contact

Ashcombe Tube Drift is an activity based business that will have customers floating down the North Saskatchewan river in Edmonton AB. The site will have all information needed and a full reservation system. The project was launched to provide people in the Edmonton area a favorite summer activity.

Here are similar websites to reference what our business will be doing and what we are looking for.

mossbankfloatco.com
quillpointpaddles.com

Target Market(s)

Families, Groups, Individuals, Anyone who wants to explore the river

Industry/Entity Type

Activities based business/ Outdoor recreational/ River Float

Coding

Coded - Design and coding required

Number of Pages Required

5+ page

Colors
0054AA
0677BA
7BADD7
CADEEF
E8F1F8
F0912C
F2A743
F7CA91
FBE8D2
FDF5EE

```html
<!DOCTYPE html>
<html lang="en">
<head>
<meta charset="utf-8">
<title>Ashcombe Tube Drift</title>
<link href="https://fonts.googleapis.com/css2?family=Fredoka:wght@600&family=Montserrat:wght@400;500;600;700&display=swap" rel="stylesheet">
<style>
:root{
  --blue:#0054AA;
  --blue-mid:#0677BA;
  --sky:#7BADD7;
  --sky-pale:#CADEEF;
  --mist:#E8F1F8;
  --orange:#F0912C;
  --orange-deep:#E9802A;
  --amber:#F2A743;
  --peach:#F7CA91;
  --cream:#FBE8D2;
  --ivory:#FDF5EE;
  --aqua:#3DC3EE;
  --night:#1E1E20;
  --navy-text:#1B2C4A;
  --body:#3b3f46;
  --field-line:#9DBCDB;
}
*{margin:0;padding:0;box-sizing:border-box}
html,body{width:1200px;height:4622px;overflow:hidden;background:#fff}
body{font-family:'Montserrat',sans-serif;color:var(--body)}
.page{position:relative;width:1200px;height:4622px;overflow:hidden}
.abs{position:absolute}
.display{font-family:'Fredoka','Montserrat',sans-serif;font-weight:600}

/* header */
.nav-bar{left:0;top:0;width:998px;height:90px;background:rgba(58,66,78,.78)}
.nav-list{left:0;top:0;height:90px;width:998px;list-style:none}
.nav-list li{position:absolute;top:38px;font-size:13px;font-weight:600;letter-spacing:.6px;color:#fff}
.nav-list li.is-active{color:var(--orange)}
.nav-list li.is-active::after{content:"";position:absolute;left:0;right:0;top:24px;height:2px;background:var(--orange)}
.call-box{left:998px;top:0;width:202px;height:90px;background:var(--orange-deep)}
.call-icon{left:2px;top:22px;width:48px;height:46px;background:var(--blue);border-radius:4px;display:flex;align-items:center;justify-content:center}
.call-label{left:60px;top:24px;font-size:11px;color:var(--navy-text);font-weight:500}
.call-number{left:60px;top:41px;font-size:14px;color:var(--navy-text);font-weight:700}
.brand-box{left:111px;top:0;width:167px;height:149px;background:#fff;border-radius:0 0 12px 12px;display:flex;flex-direction:column;align-items:center;padding-top:16px}
.brand-mark{width:62px;height:62px;border-radius:50%;background:var(--aqua)}
.brand-name{margin-top:10px;font-family:'Montserrat',sans-serif;font-weight:700;font-size:14px;line-height:17px;color:var(--blue);text-align:center;text-transform:uppercase}

/* hero */
.hero-photo{left:0;top:0;width:1200px;height:790px;background:linear-gradient(180deg,#9aa6b0 0%,#b9a57a 22%,#c98a3a 40%,#7f8a8c 58%,#a9b1b3 68%,#5a4a2a 82%,#2e3a24 100%)}
.hero-title{left:0;width:1200px;top:284px;text-align:center;font-size:56px;color:#fff;letter-spacing:1px;text-shadow:0 2px 8px rgba(0,0,0,.25)}
.hero-sub{left:0;width:1200px;top:356px;text-align:center;font-size:19px;color:#fff;font-weight:500;text-shadow:0 1px 6px rgba(0,0,0,.3)}
.hero-arrow{top:368px;color:#fff}
.hero-dots{left:572px;top:699px;display:flex;gap:8px}
.hero-dots span{width:12px;height:12px;border-radius:50%;border:1.5px solid #fff;background:rgba(255,255,255,.3)}
.hero-dots span.is-current{background:var(--orange);border-color:var(--orange)}
.wave{left:0;width:1200px}

/* pill buttons */
.pill{position:absolute;height:46px;border-radius:23px;display:flex;align-items:center;padding-left:20px;font-size:13px;font-weight:700;letter-spacing:.3px}
.pill .pill-dot{position:absolute;right:0;top:0;width:46px;height:46px;border-radius:50%;display:flex;align-items:center;justify-content:center}
.pill-orange{background:var(--orange-deep);color:var(--navy-text)}
.pill-orange .pill-dot{background:var(--blue);color:#fff}
.pill-orange-light{background:var(--orange-deep);color:#fff}
.pill-orange-light .pill-dot{background:#fff;color:var(--blue);border:2px solid var(--orange-deep)}
.pill-blue{background:var(--blue);color:#fff}
.pill-blue .pill-dot{background:#fff;color:var(--blue);border:2px solid var(--blue)}

.section-title{left:0;width:1200px;text-align:center;font-size:40px;color:var(--blue);letter-spacing:.5px}
.squiggle{width:140px;height:16px}

/* pricing */
.pricing-band{left:0;top:1101px;width:300px;height:474px;background:var(--blue)}
.pricing-photo{left:122px;top:997px;width:499px;height:682px;border-radius:6px;background:linear-gradient(180deg,#3f83c8 0%,#7fb4df 25%,#e6a29a 48%,#f2b27a 58%,#8a99a8 72%,#b9c0c6 86%,#d3d7da 100%)}
.price-card{left:648px;top:996px;width:441px;height:683px;background:var(--blue);border-radius:4px;color:#fff}
.plan-name{left:39px;top:18px;font-size:19px;font-weight:500}
.plan-price{left:39px;top:58px;font-size:56px;font-weight:500;line-height:64px}
.plan-period{left:154px;top:68px;font-size:13px;font-weight:500}
.plan-outline{left:290px;top:73px;width:151px;height:54px;border:2px solid var(--orange-deep);border-right:none;border-radius:6px 0 0 6px;display:flex;align-items:center;justify-content:center;font-size:14px;font-weight:700;letter-spacing:.4px}
.plan-copy{left:44px;top:152px;width:370px;font-size:14.5px;line-height:26px;color:#dbe6f5}
.plan-copy p+p{margin-top:11px}
.plan-list{left:48px;top:289px;list-style:none}
.plan-list li{position:relative;padding-left:23px;font-size:14px;line-height:31px;color:#f0f4fa}
.plan-list li svg{position:absolute;left:0;top:10px}
.plan-group{left:0;top:597px;width:441px;height:41px;background:var(--orange-deep);display:flex;align-items:center;justify-content:center;font-size:14px;font-weight:500;color:var(--navy-text)}
.plan-group u{text-underline-offset:2px}
.plan-note{left:0;top:655px;width:441px;text-align:center;font-size:11px;color:#dfe8f4}

/* about */
.about-fill{left:0;top:1900px;width:1200px;height:678px;background:var(--orange-deep)}
.about-title{left:110px;top:2000px;font-size:40px;color:#fff}
.about-copy{left:113px;top:2082px;width:515px;font-size:14.5px;line-height:25.8px;color:#fff;text-align:justify}
.about-photo{left:666px;top:2024px;width:450px;height:463px;border:8px solid var(--blue);border-radius:4px;background:linear-gradient(180deg,#bdb8a6 0%,#cfc8b4 18%,#8e9a72 36%,#56703c 55%,#3d5a2c 75%,#6e7366 88%,#4a4f4a 100%)}

/* faq */
.faq-list{left:213px;top:2761px;width:774px;list-style:none}
.faq-item{position:relative;height:50px;margin-bottom:22px;border:1px solid #d8dde6;border-radius:4px;background:#fff;box-shadow:0 2px 6px rgba(20,40,80,.06)}
.faq-item .q{position:absolute;left:26px;top:17px;font-size:12.5px;font-weight:700;letter-spacing:.4px;color:var(--navy-text);text-transform:uppercase}
.faq-item .toggle{position:absolute;right:24px;top:12px;font-size:18px;font-weight:700;color:var(--navy-text)}
.faq-item.is-open{height:150px;border:2px solid var(--blue)}
.faq-item .a{position:absolute;left:25px;top:46px;width:725px;font-size:14px;line-height:24.5px;color:#44484f}

/* contact */
.contact-bg{left:0;top:3441px;width:1200px;height:740px;background:linear-gradient(180deg,var(--mist) 0%,#eaf1f7 60%,#f1f5f9 100%)}
.contact-title{left:113px;top:3520px;font-size:40px;color:var(--blue)}
.contact-lead{left:113px;top:3592px;font-size:16px;color:#2c3440}
.rule{height:1px;background:#bcc9d6}
.contact-row{left:113px;display:flex;align-items:center;gap:20px;font-size:15px;color:#2c3440}
.contact-row svg{flex:none}
.contact-visit{left:113px;top:3735px;font-size:16px;line-height:25px;color:#2c3440}
.contact-map{left:111px;top:3834px;width:316px;height:158px;border:1px solid #9fb6cc;border-radius:6px;background:linear-gradient(135deg,#cfe6d3 0%,#e4efe0 45%,#d6e9f1 70%,#eef3ee 100%)}
.field{left:493px;width:494px;height:44px;border:1.5px solid var(--field-line);background:rgba(238,244,250,.9);border-radius:2px;display:flex;align-items:center;gap:10px;padding-left:14px;font-size:12.5px;color:#667}
.field.is-message{height:143px;align-items:flex-start;padding-top:14px}

/* footer */
.footer-fill{left:0;top:4150px;width:1200px;height:472px;background:var(--night)}
.footer-brand{left:232px;top:4243px;width:200px;display:flex;flex-direction:column;align-items:center}
.footer-brand .brand-mark{width:84px;height:84px}
.footer-brand .brand-name{color:#fff;font-size:17px;line-height:21px;margin-top:12px}
.listing-badge{left:244px;top:4424px;width:178px;height:30px;border-radius:15px;background:#3a3a3d}
.social{top:4476px;width:40px;height:40px;border-radius:50%;border:1.5px solid #fff}
.footer-head{top:4248px;font-size:23px;font-weight:600;color:#fff;letter-spacing:.5px}
.footer-head::after{content:"";position:absolute;left:0;top:40px;width:50px;height:3px;background:var(--aqua)}
.footer-links{left:544px;top:4322px;list-style:none}
.footer-links li{font-size:14px;line-height:31px;color:#e6e6e6}
.footer-contact{left:798px;display:flex;gap:12px}
.footer-contact .lbl{font-size:13px;color:#9aa0a8;line-height:20px}
.footer-contact .val{font-size:14px;color:#f0f0f0;line-height:22px}
.footer-rule{left:111px;top:4555px;width:978px;height:1px;background:var(--blue-mid)}
.footer-small{top:4578px;font-size:13px;color:#e6e6e6}
.to-top{left:1133px;top:4529px;width:44px;height:44px;border-radius:50%;background:var(--aqua);display:flex;align-items:center;justify-content:center}
</style>
</head>
<body>
<div class="page">

  <!-- hero -->
  <div class="abs hero-photo" role="img" aria-label="Autumn river valley with a footbridge crossing the North Saskatchewan River and golden trees"></div>
  <svg class="abs wave" style="top:600px;height:200px" viewBox="0 0 1200 200" preserveAspectRatio="none" aria-hidden="true">
    <path d="M0,62 C120,40 220,100 380,138 C520,172 600,160 680,150 C800,134 850,70 950,60 C1050,50 1120,95 1200,128 V200 H0Z" fill="var(--aqua)"/>
    <path d="M0,80 C120,58 220,118 380,156 C520,190 600,178 680,168 C800,152 850,88 950,78 C1050,68 1120,113 1200,146 V200 H0Z" fill="#fff"/>
  </svg>
  <h1 class="abs hero-title display">ASHCOMBE TUBE DRIFT</h1>
  <p class="abs hero-sub">Float the North Saskatchewan through downtown Edmonton</p>
  <a class="pill pill-orange" style="left:508px;top:409px;width:174px">BOOK NOW<span class="pill-dot"><svg width="18" height="18" viewBox="0 0 20 20"><path d="M4 10h12M11 5l5 5-5 5" stroke="currentColor" stroke-width="2" fill="none" stroke-linecap="round" stroke-linejoin="round"/></svg></span></a>
  <svg class="abs hero-arrow" style="left:42px" width="22" height="22" viewBox="0 0 20 20" aria-hidden="true"><path d="M16 10H4M9 5l-5 5 5 5" stroke="currentColor" stroke-width="2" fill="none" stroke-linecap="round" stroke-linejoin="round"/></svg>
  <svg class="abs hero-arrow" style="left:1136px" width="22" height="22" viewBox="0 0 20 20" aria-hidden="true"><path d="M4 10h12M11 5l5 5-5 5" stroke="currentColor" stroke-width="2" fill="none" stroke-linecap="round" stroke-linejoin="round"/></svg>
  <div class="abs hero-dots"><span></span><span class="is-current"></span><span></span></div>

  <!-- header -->
  <header>
    <div class="abs nav-bar"></div>
    <ul class="abs nav-list">
      <li class="is-active" style="left:519px">HOME</li>
      <li style="left:610px">PRICING</li>
      <li style="left:718px">ABOUT</li>
      <li style="left:818px">FAQ</li>
      <li style="left:897px">CONTACT</li>
    </ul>
    <div class="abs call-box">
      <div class="abs call-icon"><svg width="22" height="22" viewBox="0 0 24 24"><path d="M6.6 10.8c1.4 2.8 3.8 5.1 6.6 6.6l2.2-2.2c.3-.3.7-.4 1-.2 1.1.4 2.3.6 3.6.6.6 0 1 .4 1 1V20c0 .6-.4 1-1 1C10.6 21 3 13.4 3 4c0-.6.4-1 1-1h3.5c.6 0 1 .4 1 1 0 1.3.2 2.5.6 3.6.1.3 0 .7-.2 1z" fill="#fff"/></svg></div>
      <span class="abs call-label">Call Us</span>
      <span class="abs call-number">+1 (780) 555 0142</span>
    </div>
    <div class="abs brand-box">
      <span class="brand-mark"></span>
      <span class="brand-name">Ashcombe<br>Tube Drift</span>
    </div>
  </header>

  <!-- pricing -->
  <h2 class="abs section-title display" style="top:893px">PRICING</h2>
  <svg class="abs squiggle" style="left:530px;top:944px" viewBox="0 0 140 16" aria-hidden="true"><path d="M3 10 C25 2 45 2 70 9 S115 15 137 6" stroke="var(--orange-deep)" stroke-width="4" fill="none" stroke-linecap="round"/></svg>
  <div class="abs pricing-band"></div>
  <div class="abs pricing-photo" role="img" aria-label="Arched pedestrian bridge at sunset with the city skyline behind"></div>
  <div class="abs price-card">
    <h3 class="abs plan-name">Tube and Shuttle</h3>
    <div class="abs plan-price">$30</div>
    <span class="abs plan-period">/Month</span>
    <a class="abs plan-outline">BOOK NOW</a>
    <div class="abs plan-copy">
      <p>We keep our pricing simple and include everything you need:</p>
      <p>Premium comfort float tube with backrest and cup holder</p>
    </div>
    <ul class="abs plan-list">
      <li><svg width="13" height="11" viewBox="0 0 13 11"><path d="M1.5 5.5l3.5 3.5 6.5-7.5" stroke="var(--orange)" stroke-width="2" fill="none" stroke-linecap="round"/></svg>Lifejacket</li>
      <li><svg width="13" height="11" viewBox="0 0 13 11"><path d="M1.5 5.5l3.5 3.5 6.5-7.5" stroke="var(--orange)" stroke-width="2" fill="none" stroke-linecap="round"/></svg>Paddle</li>
      <li><svg width="13" height="11" viewBox="0 0 13 11"><path d="M1.5 5.5l3.5 3.5 6.5-7.5" stroke="var(--orange)" stroke-width="2" fill="none" stroke-linecap="round"/></svg>Round trip shuttle service</li>
      <li><svg width="13" height="11" viewBox="0 0 13 11"><path d="M1.5 5.5l3.5 3.5 6.5-7.5" stroke="var(--orange)" stroke-width="2" fill="none" stroke-linecap="round"/></svg>Safety training</li>
      <li><svg width="13" height="11" viewBox="0 0 13 11"><path d="M1.5 5.5l3.5 3.5 6.5-7.5" stroke="var(--orange)" stroke-width="2" fill="none" stroke-linecap="round"/></svg>Staff assistance</li>
      <li><svg width="13" height="11" viewBox="0 0 13 11"><path d="M1.5 5.5l3.5 3.5 6.5-7.5" stroke="var(--orange)" stroke-width="2" fill="none" stroke-linecap="round"/></svg>Parking</li>
      <li><svg width="13" height="11" viewBox="0 0 13 11"><path d="M1.5 5.5l3.5 3.5 6.5-7.5" stroke="var(--orange)" stroke-width="2" fill="none" stroke-linecap="round"/></svg>Unlimited Fun!</li>
    </ul>
    <a class="pill pill-orange-light" style="left:43px;top:534px;width:174px;height:45px">BOOK NOW<span class="pill-dot" style="height:45px;width:45px"><svg width="18" height="18" viewBox="0 0 20 20"><path d="M4 10h12M11 5l5 5-5 5" stroke="currentColor" stroke-width="2" fill="none" stroke-linecap="round" stroke-linejoin="round"/></svg></span></a>
    <div class="abs plan-group">Group of 10 or more?&nbsp;<u>Contact us</u></div>
    <div class="abs plan-note">*does not include taxes or fees</div>
  </div>

  <!-- about -->
  <svg class="abs wave" style="top:1760px;height:150px" viewBox="0 0 1200 150" preserveAspectRatio="none" aria-hidden="true">
    <path d="M0,58 C140,38 260,118 420,122 C560,126 620,58 700,32 C780,8 850,18 920,48 C1000,84 1100,68 1200,78 V150 H0Z" fill="var(--aqua)"/>
    <path d="M0,74 C140,54 260,134 420,138 C560,142 620,74 700,48 C780,24 850,34 920,64 C1000,100 1100,84 1200,94 V150 H0Z" fill="var(--orange-deep)"/>
  </svg>
  <div class="abs about-fill"></div>
  <h2 class="abs about-title display">ABOUT US</h2>
  <svg class="abs" style="left:110px;top:2046px" width="140" height="16" viewBox="0 0 140 16" aria-hidden="true"><path d="M3 10 C25 2 45 2 70 9 S115 15 137 6" stroke="#fff" stroke-width="4" fill="none" stroke-linecap="round"/></svg>
  <div class="abs about-copy">
    <p>We provide the lifejacket, paddle, river tube and shuttle service. You just have to show up.</p>
    <p>Ashcombe Tube Drift was launched to provide people in the Edmonton area a favorite summer activity. Nothing is better on a hot summer day, than spending it on the river and seeing Edmonton from a new perspective.</p>
    <p>Our home base and meeting spot is at Willow Landing (Online Map Link), by the Glasshouse Conservatory. This is where you will check in, and board the shuttle. The shuttle will take all floaters up river to Birchfield Park Boat Launch, where your tube will be waiting. Once on the river, you can sit back, relax, explore and enjoy the view. Once you</p>
  </div>
  <a class="pill pill-blue" style="left:113px;top:2445px;width:174px;height:47px">BOOK NOW<span class="pill-dot" style="width:47px;height:47px"><svg width="18" height="18" viewBox="0 0 20 20"><path d="M4 10h12M11 5l5 5-5 5" stroke="currentColor" stroke-width="2" fill="none" stroke-linecap="round" stroke-linejoin="round"/></svg></span></a>
  <div class="abs about-photo" role="img" aria-label="Summer river valley with a truss bridge, green trees and the city in the distance"></div>

  <!-- faq -->
  <h2 class="abs section-title display" style="top:2658px">FAQ</h2>
  <svg class="abs squiggle" style="left:530px;top:2706px" viewBox="0 0 140 16" aria-hidden="true"><path d="M3 10 C25 2 45 2 70 9 S115 15 137 6" stroke="var(--orange-deep)" stroke-width="4" fill="none" stroke-linecap="round"/></svg>
  <ul class="abs faq-list">
    <li class="faq-item"><span class="q">How do I reserve my float?</span><span class="toggle">+</span></li>
    <li class="faq-item"><span class="q">What safety information should I know?</span><span class="toggle">+</span></li>
    <li class="faq-item is-open"><span class="q">What is included?</span><span class="toggle">-</span>
      <p class="a">We provide round trip shuttle service and everything you need to have a fun and safe time on the river. All floaters will receive round trip shuttle service, a premium tube complete with backrest and cup holder, lifejacket, paddle, safety demonstration and fun.</p></li>
    <li class="faq-item"><span class="q">What should I bring?</span><span class="toggle">+</span></li>
    <li class="faq-item"><span class="q">Where are you located?</span><span class="toggle">+</span></li>
    <li class="faq-item"><span class="q">What time should I arrive?</span><span class="toggle">+</span></li>
  </ul>
  <a class="pill pill-orange" style="left:513px;top:3305px;width:174px;height:48px">VIEW ALL<span class="pill-dot" style="width:48px;height:48px"><svg width="18" height="18" viewBox="0 0 20 20"><path d="M4 10h12M11 5l5 5-5 5" stroke="currentColor" stroke-width="2" fill="none" stroke-linecap="round" stroke-linejoin="round"/></svg></span></a>

  <!-- contact -->
  <div class="abs contact-bg"></div>
  <h2 class="abs contact-title display">GET IN TOUCH</h2>
  <svg class="abs" style="left:113px;top:3567px" width="110" height="14" viewBox="0 0 140 16" aria-hidden="true"><path d="M3 10 C25 2 45 2 70 9 S115 15 137 6" stroke="var(--orange-deep)" stroke-width="4" fill="none" stroke-linecap="round"/></svg>
  <p class="abs contact-lead">We’d love to hear from you!</p>
  <div class="abs rule" style="left:113px;top:3631px;width:340px"></div>
  <div class="abs contact-row" style="top:3646px"><svg width="18" height="18" viewBox="0 0 24 24"><path d="M6.6 10.8c1.4 2.8 3.8 5.1 6.6 6.6l2.2-2.2c.3-.3.7-.4 1-.2 1.1.4 2.3.6 3.6.6.6 0 1 .4 1 1V20c0 .6-.4 1-1 1C10.6 21 3 13.4 3 4c0-.6.4-1 1-1h3.5c.6 0 1 .4 1 1 0 1.3.2 2.5.6 3.6.1.3 0 .7-.2 1z" fill="var(--blue)"/></svg>780 555 0186</div>
  <div class="abs contact-row" style="top:3682px"><svg width="18" height="14" viewBox="0 0 18 14"><rect x="1" y="1" width="16" height="12" rx="1.5" fill="var(--blue)"/><path d="M1.5 2l7.5 6 7.5-6" stroke="#fff" stroke-width="1.4" fill="none"/></svg>info@ashcombetubedrift.com</div>
  <div class="abs rule" style="left:113px;top:3719px;width:340px"></div>
  <p class="abs contact-visit">Come visit us on float days at<br>Willow Landing</p>
  <div class="abs contact-row" style="top:3802px"><svg width="16" height="20" viewBox="0 0 16 20"><path d="M8 0C3.6 0 0 3.5 0 7.9 0 13.5 8 20 8 20s8-6.5 8-12.1C16 3.5 12.4 0 8 0z" fill="var(--blue)"/><circle cx="8" cy="7.8" r="3" fill="#fff"/></svg>4120 Riverbend Way NW, Edmonton, AB</div>
  <div class="abs contact-map" role="img" aria-label="Street map showing the meeting point beside the river"></div>

  <div class="abs field" style="top:3531px"><svg width="12" height="13" viewBox="0 0 12 13"><circle cx="6" cy="3.5" r="3" fill="var(--orange)"/><path d="M0 13c0-3.5 2.7-5.5 6-5.5s6 2 6 5.5z" fill="var(--orange)"/></svg>First Name</div>
  <div class="abs field" style="top:3601px"><svg width="15" height="11" viewBox="0 0 15 11"><rect width="15" height="11" rx="1" fill="var(--orange)"/><path d="M.5 1l7 5 7-5" stroke="#fff" stroke-width="1.2" fill="none"/></svg>Email</div>
  <div class="abs field" style="top:3671px"><svg width="13" height="13" viewBox="0 0 24 24"><path d="M6.6 10.8c1.4 2.8 3.8 5.1 6.6 6.6l2.2-2.2c.3-.3.7-.4 1-.2 1.1.4 2.3.6 3.6.6.6 0 1 .4 1 1V20c0 .6-.4 1-1 1C10.6 21 3 13.4 3 4c0-.6.4-1 1-1h3.5c.6 0 1 .4 1 1 0 1.3.2 2.5.6 3.6.1.3 0 .7-.2 1z" fill="var(--orange)"/></svg>Phone</div>
  <div class="abs field is-message" style="top:3741px"><svg width="12" height="12" viewBox="0 0 12 12"><path d="M1 1l8 8" stroke="var(--orange)" stroke-width="2.4" stroke-linecap="round"/><path d="M9.5 9.5l1.5 1.5" stroke="var(--orange)" stroke-width="1.4"/></svg>Message</div>
  <a class="pill pill-orange" style="left:493px;top:3918px;width:174px;height:45px">SUBMIT<span class="pill-dot" style="width:45px;height:45px"><svg width="18" height="18" viewBox="0 0 20 20"><path d="M4 10h12M11 5l5 5-5 5" stroke="currentColor" stroke-width="2" fill="none" stroke-linecap="round" stroke-linejoin="round"/></svg></span></a>

  <!-- footer -->
  <svg class="abs wave" style="top:4030px;height:160px" viewBox="0 0 1200 160" preserveAspectRatio="none" aria-hidden="true">
    <path d="M0,68 C120,58 200,118 330,123 C470,128 560,40 700,20 C820,5 880,68 980,83 C1080,98 1140,80 1200,74 V160 H0Z" fill="var(--aqua)"/>
    <path d="M0,84 C120,74 200,134 330,139 C470,144 560,56 700,36 C820,21 880,84 980,99 C1080,114 1140,96 1200,90 V160 H0Z" fill="var(--night)"/>
  </svg>
  <div class="abs footer-fill"></div>
  <div class="abs footer-brand">
    <span class="brand-mark"></span>
    <span class="brand-name">Ashcombe<br>Tube Drift</span>
  </div>
  <div class="abs listing-badge"></div>
  <span class="abs social" style="left:292px"></span>
  <span class="abs social" style="left:341px"></span>

  <h4 class="abs footer-head" style="left:538px">QUICK LINKS</h4>
  <ul class="abs footer-links">
    <li>Home</li>
    <li>Our Services</li>
    <li>About Us</li>
    <li>Testimonials</li>
    <li>Contact Us</li>
  </ul>

  <h4 class="abs footer-head" style="left:798px">CONTACT US</h4>
  <div class="abs footer-contact" style="top:4324px">
    <svg width="18" height="24" viewBox="0 0 16 20"><path d="M8 0C3.6 0 0 3.5 0 7.9 0 13.5 8 20 8 20s8-6.5 8-12.1C16 3.5 12.4 0 8 0z" fill="var(--aqua)"/><circle cx="8" cy="7.8" r="3" fill="var(--night)"/></svg>
    <div><div class="lbl">Address</div><div class="val">4120 Riverbend Way NW,<br>Edmonton, AB</div></div>
  </div>
  <div class="abs footer-contact" style="top:4405px">
    <svg width="20" height="15" viewBox="0 0 15 11" style="margin-top:6px"><rect width="15" height="11" rx="1" fill="var(--aqua)"/><path d="M.5 1l7 5 7-5" stroke="var(--night)" stroke-width="1.2" fill="none"/></svg>
    <div><div class="lbl">Email</div><div class="val">info@ashcombetubedrift.com</div></div>
  </div>
  <div class="abs footer-contact" style="top:4461px">
    <svg width="20" height="20" viewBox="0 0 24 24" style="margin-top:8px"><path d="M6.6 10.8c1.4 2.8 3.8 5.1 6.6 6.6l2.2-2.2c.3-.3.7-.4 1-.2 1.1.4 2.3.6 3.6.6.6 0 1 .4 1 1V20c0 .6-.4 1-1 1C10.6 21 3 13.4 3 4c0-.6.4-1 1-1h3.5c.6 0 1 .4 1 1 0 1.3.2 2.5.6 3.6.1.3 0 .7-.2 1z" fill="var(--aqua)"/></svg>
    <div><div class="lbl">Phone</div><div class="val">+1 (780) 555 0173</div></div>
  </div>

  <div class="abs footer-rule"></div>
  <p class="abs footer-small" style="left:111px">©2022.All rights reserved.</p>
  <p class="abs footer-small" style="right:111px">Sign up for our mailing list</p>
  <a class="abs to-top"><svg width="16" height="16" viewBox="0 0 20 20"><path d="M5 12l5-5 5 5" stroke="#fff" stroke-width="2" fill="none" stroke-linecap="round" stroke-linejoin="round"/></svg></a>
</div>
</body>
</html>
```